Board to put on a meditation centre - Lantern Grove

I need a board design for a new meditation centre based in Oslo which offers free courses in meditation and self-empowerment. The size of the board is width 374cm x height 104cm.  The name of the meditation centre together with subtitles should be on the board but also some elegant decoration that matches the theme (lantern grove/meditation).
Here is the website of the meditation centre to give you a feeling of it: https://kvitfjellsenteret.no/
Good if you can use a blue color close to this one: rgb(37, 180, 193) as well as some brown/golden color (similar to the palette on the website).
On the board it should say:
Kveldens lund (in big letters, the rest is subtitles)
Meditasjon & Spirituell visdom
Kurs - Retreat - Dialog
kvitfjellsenteret.no
The design should be very elegant and beautiful and the feeling should be of "A Lantern Grove". A logo is here attached and should be used but I need to get a better quality version of it, will upload that as soon as possible.

```html
<!DOCTYPE html>
<html lang="no">
<head>
<meta charset="utf-8">
<title>Kveldens lund – skilt</title>
<link href="https://fonts.googleapis.com/css2?family=Poppins:wght@500;600;700;800&display=swap" rel="stylesheet">
<style>
  :root {
    --teal: #25b4c1;
    --gold: #c8963e;
    --gold-deep: #a8782c;
    --brown: #3b2a20;
    --white: #ffffff;
    --page: #ffffff;
    --muted: #8a7563;
    --glow-light: #f6ead2;
    --glow-mid: #e3c58e;
    --glow-deep: #b88a4a;
  }
  * { box-sizing: border-box; margin: 0; padding: 0; }
  html, body {
    width: 1110px; height: 1200px; overflow: hidden;
    background: var(--page);
    font-family: "Poppins", sans-serif;
  }
  .board {
    position: absolute; left: 0; top: 446px;
    width: 1110px; height: 308px;
    background: var(--white);
    overflow: hidden;
    box-shadow: 0 10px 28px rgba(0,0,0,0.22);
  }
  .board__band {
    position: absolute; left: 0; top: 0; width: 1110px; height: 136px;
    background: var(--teal);
  }
  .board__shapes, .board__photo { position: absolute; left: 0; top: 0; }
  .board__title {
    position: absolute; left: 58px; top: 4px;
    font-weight: 800; font-size: 80px; line-height: 1.2; letter-spacing: -1px;
    color: var(--white); white-space: nowrap;
  }
  .board__title em { font-style: normal; color: var(--gold); }
  .board__subtitle {
    position: absolute; left: 59px; top: 112px; width: 706px; height: 56px;
    background: var(--brown); border-radius: 12px;
    color: var(--white); font-weight: 700; font-size: 31px;
    line-height: 56px; text-align: center; white-space: nowrap;
  }
  .offers {
    position: absolute; left: 62px; top: 187px; height: 48px;
    display: flex; align-items: center;
  }
  .offer { display: flex; align-items: center; margin-right: 26px; }
  .offer__icon {
    width: 48px; height: 48px; border-radius: 50%;
    background: var(--teal); border: 2px solid var(--gold);
    display: flex; align-items: center; justify-content: center;
  }
  .offer__label {
    margin-left: 9px; font-weight: 700; font-size: 25px; color: var(--brown);
  }
  .offers__divider {
    width: 1px; height: 48px; background: #d6cbbd; margin: 0 22px 0 -4px;
  }
  .partner { display: flex; align-items: center; }
  .partner__dot { width: 26px; height: 26px; border-radius: 50%; background: var(--gold); margin-right: 10px; }
  .partner__name {
    font-weight: 500; font-size: 14px; letter-spacing: 2px;
    color: var(--muted); text-transform: uppercase; white-space: nowrap;
  }
  .web {
    position: absolute; left: 60px; top: 265px; height: 43px;
    display: flex; align-items: center; text-decoration: none;
    color: var(--white); font-size: 21px; letter-spacing: 2.2px; font-weight: 500;
  }
  .web svg { margin-right: 12px; }
  .web strong { font-weight: 700; }
</style>
</head>
<body>
  <section class="board">
    <div class="board__band"></div>

    <svg class="board__shapes" width="1110" height="308" viewBox="0 0 1110 308">
      <polygon points="560,281 1110,281 1110,308 572,308" fill="var(--brown)"/>
      <polygon points="0,265 550,265 572,308 0,308" fill="var(--gold)"/>
    </svg>

    <svg class="board__photo" width="1110" height="308" viewBox="0 0 1110 308"
         role="img" aria-label="Fotografi av en mediterende kvinne i yogastilling foran et lyst, varmt lanternelys i en lund">
      <defs>
        <radialGradient id="lanternGlow" cx="0.62" cy="0.42" r="0.75">
          <stop offset="0" stop-color="var(--glow-light)"/>
          <stop offset="0.55" stop-color="var(--glow-mid)"/>
          <stop offset="1" stop-color="var(--glow-deep)"/>
        </radialGradient>
      </defs>
      <polygon points="830,0 1110,0 1110,281 895,281 838,250 880,140 812,60" fill="url(#lanternGlow)"/>
    </svg>

    <h1 class="board__title">KVELDENS <em>LUND</em></h1>
    <p class="board__subtitle">MEDITASJON &amp; SPIRITUELL VISDOM</p>

    <div class="offers">
      <div class="offer">
        <span class="offer__icon">
          <svg width="24" height="24" viewBox="0 0 24 24" fill="none" stroke="#fff" stroke-width="2" stroke-linecap="round">
            <path d="M6 4h9a3 3 0 0 1 3 3v13H9a3 3 0 0 1-3-3z"/><path d="M6 17a3 3 0 0 1 3-3h9"/>
          </svg>
        </span>
        <span class="offer__label">Kurs</span>
      </div>
      <div class="offer">
        <span class="offer__icon">
          <svg width="26" height="24" viewBox="0 0 26 24" fill="none" stroke="#fff" stroke-width="2" stroke-linejoin="round">
            <path d="M13 4c3 3 3 9 0 14c-3-5-3-11 0-14z"/><path d="M13 18c-4 0-8-3-9-8c4 0 7 2 9 8z"/><path d="M13 18c4 0 8-3 9-8c-4 0-7 2-9 8z"/>
          </svg>
        </span>
        <span class="offer__label">Retreat</span>
      </div>
      <div class="offer">
        <span class="offer__icon">
          <svg width="24" height="24" viewBox="0 0 24 24" fill="none" stroke="#fff" stroke-width="2" stroke-linejoin="round">
            <path d="M4 5h12v8H9l-4 3v-3H4z"/><path d="M18 9h2v8h-1v3l-4-3h-5v-2"/>
          </svg>
        </span>
        <span class="offer__label">Dialog</span>
      </div>
      <span class="offers__divider"></span>
      <div class="partner">
        <span class="partner__dot"></span>
        <span class="partner__name">Solvang Stillhetshus</span>
      </div>
    </div>

    <a class="web" href="https://kvitfjellsenteret.no/">
      <svg width="24" height="24" viewBox="0 0 24 24" fill="none" stroke="#fff" stroke-width="1.8">
        <circle cx="12" cy="12" r="10"/><ellipse cx="12" cy="12" rx="4.5" ry="10"/><path d="M2 12h20M4 7h16M4 17h16"/>
      </svg>
      <span>WWW.<strong>KVITFJELLSENTERET</strong>.NO</span>
    </a>
  </section>
</body>
</html>
```